Inspirational Quotes Poster Set

Brookloft is a stylish coworking space, which has a design-oriented vintage look from the 60's with an industrial touch (www.brookloft-example.com) Brookloft Quote Poster Set of 16 posters. The poster should be typo oriented and rather simple. Reflecting a bit the clean billboard design from the sixties. Minimal / simple graphical elements

Target Market(s)

Startups and Entrepreneurs

Industry/Entity Type

Startup

Font styles to use
Sans Serif

Colors

Designer to choose colors to be used in the design.

Requirements
Must have
• Posters need to be on and very stylish

```html
<!DOCTYPE html>
<html lang="en">
<head>
<meta charset="utf-8">
<title>Brookloft Quote Poster Set – Doing Things</title>
<link rel="stylesheet" href="https://fonts.googleapis.com/css2?family=Bricolage+Grotesque:opsz,wght@12..96,700;12..96,800&display=swap">
<style>
  :root {
    --pitch: #14a19a;
    --pitch-light: #18aaa3;
    --chalk: #ffffff;
  }
  * { margin: 0; padding: 0; box-sizing: border-box; }
  html, body { width: 801px; height: 1200px; overflow: hidden; background: var(--pitch); }
  .poster {
    position: relative;
    width: 801px;
    height: 1200px;
    background: var(--pitch);
    color: var(--chalk);
    font-family: "Bricolage Grotesque", sans-serif;
    overflow: hidden;
  }
  .pitch-diagram {
    position: absolute;
    inset: 0;
    background: radial-gradient(ellipse at 50% 50%, var(--pitch-light) 0%, var(--pitch) 70%);
  }
  .lead-in {
    position: absolute;
    left: 70px;
    top: 404px;
    font-size: 57px;
    font-weight: 800;
    line-height: 50px;
    letter-spacing: -0.5px;
  }
  .headline {
    position: absolute;
    left: 52px;
    top: 644px;
    font-size: 204px;
    font-weight: 800;
    line-height: 161px;
    letter-spacing: -7px;
  }
  .attribution {
    position: absolute;
    left: 70px;
    top: 1014px;
    font-size: 26px;
    font-weight: 800;
    line-height: 28px;
  }
  .brand-name {
    position: absolute;
    left: 0;
    width: 801px;
    top: 1104px;
    text-align: center;
    font-size: 42px;
    font-weight: 800;
    letter-spacing: -1px;
  }
</style>
</head>
<body>
<main class="poster">
  <div class="pitch-diagram" role="img" aria-label="Football pitch tactics diagram with a dashed passing run between two player markers"></div>

  <p class="lead-in">we have a<br>strategic plan<br>it’s called</p>
  <h1 class="headline">doing<br>things</h1>
  <p class="attribution">Hal Brennan,<br>Co Founder &amp; CEO Northway Airlines</p>
  <p class="brand-name">brookloft</p>
</main>
</body>
</html>
```